Homeowners Insurance Provider Website

We are selling homeowners insurance policy / tenants Policy/Flood Insurance in USA in few states and planning expand nationally.

Our target audience are two folds: Customers (Buy policies) and Insurance Agents who wants to work with us to sell our policies to customers. But website should focus 80% on customers and 20% on agents. So, more customer focused user experience. Please note that there is no direct buy option for customers. They always go through insurance agents.

Customer focused, educational that makes buyer journey easy. We don’t want to come off as trying sell something as there is no direct sales involved from website.

Target Market(s)

Homeowners in USA and Insurance agent who sells these insurance.

Industry/Entity Type

Insurance

Number of Pages Required

4 page

Font styles to use
Other font styles liked:
• Open to suggestions

Colors

Designer to choose colors to be used in the design.

Requirements
Must have
• Three most important things: Trustworthy, Authentic, Simple
• Please use colors form logo and grays
• We like: www.hollowmere.com
• https://www.quillfenbrook.com/
• We need Agent Look up tool on home page similar to what is shown on example sites.
• Design:
• Home Page - Open to Ideas
• Insurance (Products) Landing Page - Info similar to: https://www.quillfenbrook.com/insurance/
• Agents Page - https://www.quillfenbrook.com/agents/
• Claims Page - Information similar to: https://www.quillfenbrook.com/claims-center/
• Site Navigation:
• Home
• Insurance
• Claims
• Agents
• About Us
• Contact Us
Nice to have
• Elegant, minimal and clean design that reflects trust and authenticity.
Should not have
• Slider or rotating images - prefer flat design. Not over powering design.

```html
<!DOCTYPE html>
<html lang="en">
<head>
<meta charset="utf-8">
<title>Hearthline Insurance Co.</title>
<link rel="stylesheet" href="https://fonts.googleapis.com/css2?family=Open+Sans:wght@400;600;700;800&family=Raleway:wght@400;500;600&display=swap">
<style>
:root{
  --red:#e0202e;
  --red-dark:#c81b28;
  --blue:#253d7d;
  --navy:#172852;
  --ink:#222;
  --text:#555;
  --gray-bg:#f3f3f3;
  --line:#cfcfcf;
  --footer:#1c1c1c;
  --white:#fff;
}
*{box-sizing:border-box;margin:0;padding:0}
html,body{width:1200px;height:2903px;overflow:hidden}
body{position:relative;font-family:"Raleway",sans-serif;color:var(--text);background:var(--white)}
.abs{position:absolute}
.btn{position:absolute;display:flex;align-items:center;justify-content:center;font-family:"Open Sans",sans-serif;font-weight:600;font-size:13px;color:var(--white);text-transform:uppercase;letter-spacing:.3px}
.btn-blue{background:var(--blue)}
.btn-red{background:var(--red)}
.btn-white{background:var(--white);color:var(--red)}

/* hero */
.hero{position:absolute;left:0;top:0;width:1200px;height:548px;background:linear-gradient(120deg,#cfc9bf 0%,#9b8f80 35%,#5d6172 70%,#3d3f46 100%)}
.topbar{position:absolute;left:141px;top:35px;width:917px;height:85px;background:rgba(255,255,255,.88);display:flex;align-items:center;padding:0 22px}
.brand{display:flex;align-items:center;gap:10px;font-family:"Open Sans",sans-serif;font-weight:700;font-size:21px;color:var(--blue)}
.brand-mark{width:30px;height:30px;background:var(--blue)}
.nav{margin-left:auto;display:flex;align-items:center;gap:19px;font-family:"Open Sans",sans-serif;font-size:13px;color:#333}
.nav .active{color:var(--red)}
.nav .quote{background:var(--blue);color:var(--white);padding:7px 9px}

/* feature circles */
.feature{position:absolute;width:186px;text-align:center}
.feature .ring{width:186px;height:186px;border-radius:50%;background:rgba(255,255,255,.55);display:flex;align-items:center;justify-content:center}
.feature .disc{width:158px;height:158px;border-radius:50%;background:var(--white);border:1px solid #e2e2e2;display:flex;align-items:center;justify-content:center}
.feature-label{position:absolute;width:240px;text-align:center;font-family:"Open Sans",sans-serif;font-weight:600;font-size:15px;color:var(--red);line-height:22px;text-transform:uppercase}

/* headings */
.h2{font-family:"Open Sans",sans-serif;font-weight:600;font-size:25px;color:var(--ink);letter-spacing:.5px}
.para{font-size:12.5px;line-height:22px}

/* quote form */
.quote-box{position:absolute;left:818px;top:720px;width:240px;height:282px;background:#eeeeee;border:1px solid #dcdcdc}
.quote-box h3{height:35px;background:var(--blue);color:var(--white);font-family:"Open Sans",sans-serif;font-weight:600;font-size:21px;text-align:center;line-height:35px}
.field{position:absolute;background:#f7f7f7;border:1px solid #d6d6d6;font-size:11px;color:#888;padding:0 9px;display:flex;align-items:center}

/* split band */
.band-red{position:absolute;left:0;top:1058px;width:600px;height:327px;background:var(--red)}
.band-blue{position:absolute;left:600px;top:1058px;width:600px;height:327px;background:var(--blue)}
.band-title{position:absolute;font-family:"Open Sans",sans-serif;font-weight:700;font-size:18px;color:var(--white)}
.band-text{position:absolute;width:330px;font-size:12.5px;line-height:20.5px;color:var(--white)}
.band-emblem{position:absolute;left:510px;top:1110px;width:180px;height:180px;border-radius:50%;background:var(--white);display:flex;align-items:center;justify-content:center;font-family:"Open Sans",sans-serif;font-weight:700;font-size:19px;color:var(--blue)}

/* insurance */
.insurance{position:absolute;left:0;top:1385px;width:1200px;height:627px;background:var(--gray-bg)}
.card{position:absolute;top:1542px;width:306px;height:414px;overflow:hidden}
.card-photo{position:absolute;inset:0}
.card-shade{position:absolute;left:0;right:0;bottom:0;height:190px;background:linear-gradient(to bottom,rgba(0,0,0,0),rgba(0,0,0,.85) 40%)}
.card-panel{position:absolute;left:0;right:0;bottom:0;height:214px;background:rgba(37,61,125,.88)}
.card-title{position:absolute;left:0;right:0;text-align:center;font-family:"Open Sans",sans-serif;font-weight:600;font-size:20px;color:var(--white)}
.card-rule{position:absolute;left:138px;width:30px;height:2px;background:var(--red)}
.card-text{position:absolute;left:22px;right:22px;text-align:center;font-size:11px;line-height:19px;color:#eee}

/* agent finder */
.finder{position:absolute;left:0;top:2012px;width:1200px;height:293px;background:var(--navy)}

/* claim + contact */
.input{position:absolute;height:31px;border:1px solid #cfcfcf;font-size:11px;color:#777;padding:0 10px;display:flex;align-items:center}

/* footer */
.footer{position:absolute;left:0;top:2618px;width:1200px;height:250px;background:var(--footer)}
.f-title{position:absolute;font-family:"Raleway",sans-serif;font-size:16px;color:var(--white)}
.f-rule{position:absolute;height:1px;background:#444}
.f-links{position:absolute;list-style:none;font-size:11px;color:#ccc;line-height:22px}
.f-links li::before{content:"› ";color:#888}
.f-small{position:absolute;font-size:11px;color:#bbb;line-height:18px}
.copy{position:absolute;left:0;top:2868px;width:1200px;height:35px;background:var(--blue)}
.social{position:absolute;top:9px;width:19px;height:19px;border:1px solid #fff;background:#1f6fb8}
</style>
</head>
<body>

<!-- hero -->
<section class="hero" role="img" aria-label="Photo of a smiling senior couple shaking hands with an insurance agent in a home library"></section>
<header class="topbar">
  <div class="brand"><span class="brand-mark"></span>Hearthline Insurance Co.</div>
  <nav class="nav">
    <span class="active">Home</span><span>About Us</span><span>Insurance</span><span>Agents</span><span>Claims</span><span>Contact Us</span><span class="quote">Get a quote</span>
  </nav>
</header>

<!-- policy features -->
<div class="feature" style="left:222px;top:452px"><div class="ring"><div class="disc">
  <svg width="58" height="58" viewBox="0 0 58 58"><path d="M8 28 L29 10 L50 28 L45 28 L45 44 L13 44 L13 28 Z" fill="#e0202e"/><circle cx="29" cy="30" r="7" fill="#fff"/><path d="M4 50 H40 L50 44" stroke="#e0202e" stroke-width="4" fill="none"/></svg>
</div></div></div>
<div class="feature" style="left:505px;top:452px"><div class="ring"><div class="disc">
  <svg width="58" height="58" viewBox="0 0 58 58"><path d="M5 26 L29 6 L53 26 L48 26 L48 50 L10 50 L10 26 Z" fill="#e0202e"/><circle cx="23" cy="27" r="4" fill="#fff"/><circle cx="35" cy="27" r="4" fill="#fff"/><rect x="19" y="33" width="8" height="15" fill="#fff"/><rect x="31" y="33" width="8" height="15" fill="#fff"/></svg>
</div></div></div>
<div class="feature" style="left:789px;top:452px"><div class="ring"><div class="disc">
  <svg width="58" height="58" viewBox="0 0 58 58"><path d="M8 26 L29 8 L50 26 L45 26 L45 40 L13 40 L13 26 Z" fill="#e0202e"/><rect x="25" y="28" width="8" height="12" fill="#fff"/><path d="M6 46 q6-5 12 0 t12 0 t12 0 t12 0" stroke="#e0202e" stroke-width="3" fill="none"/><path d="M6 53 q6-5 12 0 t12 0 t12 0 t12 0" stroke="#e0202e" stroke-width="3" fill="none"/></svg>
</div></div></div>
<div class="feature-label" style="left:195px;top:633px">Homeowners<br>Policy</div>
<div class="feature-label" style="left:478px;top:644px">Tenants Policy</div>
<div class="feature-label" style="left:762px;top:644px">Flood Insurance</div>

<!-- about -->
<h2 class="h2 abs" style="left:141px;top:730px">ABOUT US</h2>
<div class="abs" style="left:141px;top:786px;width:617px;height:1px;background:var(--line)"></div>
<div class="abs" style="left:141px;top:784px;width:62px;height:4px;background:var(--blue)"></div>
<p class="para abs" style="left:145px;top:806px;width:612px">Lorem ipsum dolor sit amet, consectetuer adipiscing elit, sed diam nonummy nibh euismod tincidunt ut laoreet dolore magna aliquam erat volutpat. Ut wisi enim ad minim veniam, quis nostrud exerci tation ullamcorper suscipit lobortis nisl ut aliquip ex ea commodo consequat. Duis autem vel eum iriure dolor in hendrerit in vulputate velit esse molestie consequat, vel illum dolore eu feugiat nulla facilisis at vero eros et accumsan et iusto odio dignissim qui blandit praesent luptatum zzril delenit augue duis dolore te feugait nulla facilisi.</p>
<div class="btn btn-blue" style="left:141px;top:971px;width:131px;height:29px">Read More</div>

<aside class="quote-box">
  <h3>Get A Quote</h3>
  <div class="field" style="left:14px;top:56px;width:210px;height:32px">Name</div>
  <div class="field" style="left:14px;top:93px;width:210px;height:32px">Email</div>
  <div class="field" style="left:14px;top:130px;width:210px;height:32px">Subject</div>
  <div class="field" style="left:14px;top:167px;width:210px;height:50px">Message</div>
  <div class="btn btn-blue" style="left:14px;top:228px;width:210px;height:30px">Submit</div>
</aside>

<!-- customers / agents -->
<section class="band-red"></section>
<section class="band-blue"></section>
<h3 class="band-title" style="left:141px;top:1110px">Customers</h3>
<p class="band-text" style="left:141px;top:1143px">Lorem ipsum dolor sit amet, consectetuer adipiscing elit, sed diam nonummy nibh euismod tincidunt ut laoreet dolore magna aliquam erat volutpat. Ut wisi enim ad minim veniam, quis nostrud exerci tation ullamcorper suscipit lobortis nisl ut aliquip ex ea commodo consequat. Duis autem vel eum iriure dolor in hendrerit in vulputate velit esse molestie consequat.</p>
<div class="btn btn-blue" style="left:141px;top:1302px;width:131px;height:29px">Learn More</div>
<h3 class="band-title" style="right:142px;top:1110px">Agents</h3>
<p class="band-text" style="left:728px;top:1143px;text-align:right">Lorem ipsum dolor sit amet, consectetuer adipiscing elit, sed diam nonummy nibh euismod tincidunt ut laoreet dolore magna aliquam erat volutpat. Ut wisi enim ad minim veniam, quis nostrud exerci tation ullamcorper suscipit lobortis nisl ut aliquip ex ea commodo consequat. Duis autem vel eum iriure dolor in hendrerit in vulputate velit esse molestie consequat.</p>
<div class="btn btn-red" style="left:928px;top:1302px;width:130px;height:29px">Learn More</div>
<div class="band-emblem">Hearthline</div>

<!-- insurance -->
<section class="insurance"></section>
<h2 class="h2 abs" style="left:0;width:1200px;text-align:center;top:1430px">INSURANCE</h2>
<div class="abs" style="left:292px;top:1488px;width:616px;height:1px;background:var(--line)"></div>
<div class="abs" style="left:569px;top:1486px;width:62px;height:4px;background:var(--blue)"></div>

<article class="card" style="left:141px">
  <div class="card-photo" role="img" aria-label="Photo of a couple looking around a bright new home" style="background:linear-gradient(160deg,#f0efec,#c9c4bd 60%,#8a7a6c)"></div>
  <div class="card-shade"></div>
  <h3 class="card-title" style="top:235px">Homeowner Policy</h3>
  <div class="card-rule" style="top:268px"></div>
  <p class="card-text" style="top:285px">Lorem ipsum dolor sit amet, consectetuer adipiscing elit, sed diam nonummy nibh euismod tincidunt ut laoreet dolore magna aliquam erat volutpat.</p>
  <div class="btn btn-red" style="left:29px;top:360px;width:109px;height:29px">Quote →</div>
  <div class="btn btn-blue" style="left:146px;top:360px;width:132px;height:29px">Read More →</div>
</article>
<article class="card" style="left:447px">
  <div class="card-photo" role="img" aria-label="Photo of a young smiling couple reviewing papers together" style="background:linear-gradient(160deg,#e9e3d6,#c7a98d 55%,#6b5a4d)"></div>
  <div class="card-panel"></div>
  <h3 class="card-title" style="top:225px">Tenant Policy</h3>
  <div class="card-rule" style="top:258px"></div>
  <p class="card-text" style="top:273px">Lorem ipsum dolor sit amet, consectetuer adipiscing elit, sed diam nonummy nibh euismod tincidunt ut laoreet dolore magna aliquam erat volutpat.</p>
  <div class="btn btn-red" style="left:29px;top:348px;width:109px;height:29px">Quote →</div>
  <div class="btn btn-white" style="left:146px;top:348px;width:132px;height:29px">Read More →</div>
</article>
<article class="card" style="left:753px">
  <div class="card-photo" role="img" aria-label="Photo of a red wooden house collapsed by floodwater among trees" style="background:linear-gradient(160deg,#6d8a4f,#44603a 50%,#5a3a32)"></div>
  <div class="card-shade"></div>
  <h3 class="card-title" style="top:235px">Flood Policy</h3>
  <div class="card-rule" style="top:268px"></div>
  <p class="card-text" style="top:285px">Lorem ipsum dolor sit amet, consectetuer adipiscing elit, sed diam nonummy nibh euismod tincidunt ut laoreet dolore magna aliquam erat volutpat.</p>
  <div class="btn btn-red" style="left:29px;top:360px;width:109px;height:29px">Quote →</div>
  <div class="btn btn-blue" style="left:146px;top:360px;width:132px;height:29px">Read More →</div>
</article>

<!-- find an agent -->
<section class="finder"></section>
<h2 class="h2 abs" style="left:0;width:1200px;text-align:center;top:2060px;color:var(--white)">FIND AN AGENT</h2>
<div class="abs" style="left:569px;top:2112px;width:62px;height:3px;background:var(--white)"></div>
<p class="para abs" style="left:292px;top:2134px;width:616px;text-align:center;color:var(--white)">Lorem ipsum dolor sit amet, consectetuer adipiscing elit, sed diam nonummy nibh euismod tincidunt ut laoreet dolore magna aliquam erat volutpat. Ut wisi enim ad minim veniam, quis nostrud exerci tation ullamcorper suscipit lobortis nisl ut aliquip ex ea commodo consequat.</p>
<div class="input" style="left:439px;top:2233px;width:157px;height:29px;background:var(--white);border:0">Search...</div>
<div class="btn btn-red" style="left:604px;top:2233px;width:157px;height:29px">Find An Agent</div>

<!-- claim -->
<h3 class="abs" style="left:140px;top:2356px;width:300px;text-align:center;font-family:'Open Sans',sans-serif;font-weight:600;font-size:26px;color:var(--navy)">Report And Check</h3>
<div class="abs" style="left:140px;top:2390px;width:300px;text-align:center;font-family:'Open Sans',sans-serif;font-weight:800;font-size:58px;color:var(--red);line-height:64px">A Claim</div>
<p class="abs" style="left:140px;top:2460px;width:300px;text-align:center;font-size:14px;line-height:23px;color:#333">Login To Report A Claim Or<br>Check Your Claim Status.</p>
<div class="btn btn-red" style="left:238px;top:2531px;width:86px;height:29px">Login</div>

<!-- contact form -->
<h2 class="h2 abs" style="left:486px;top:2350px;font-size:24px">CONTACT FORM</h2>
<div class="abs" style="left:486px;top:2400px;width:572px;height:1px;background:var(--line)"></div>
<div class="abs" style="left:486px;top:2398px;width:62px;height:4px;background:var(--blue)"></div>
<p class="abs" style="left:486px;top:2414px;font-size:11px;color:#555">Please fill up bellow form</p>
<div class="input" style="left:486px;top:2438px;width:256px">Name</div>
<div class="input" style="left:753px;top:2438px;width:258px">Email</div>
<div class="input" style="left:486px;top:2484px;width:256px">Phone</div>
<div class="input" style="left:753px;top:2484px;width:258px">Message</div>
<div class="btn btn-red" style="left:486px;top:2531px;width:84px;height:29px">Submit</div>

<!-- footer -->
<footer class="footer"></footer>
<h4 class="f-title" style="left:159px;top:2658px">Quick Links</h4>
<div class="f-rule" style="left:159px;top:2686px;width:100px"></div>
<ul class="f-links" style="left:159px;top:2694px">
  <li style="color:var(--blue)">Home</li><li>About Us</li><li>Insurance</li><li>Agents</li><li>Claims</li><li>Contact Us</li>
</ul>
<h4 class="f-title" style="left:339px;top:2658px">Contact Detail</h4>
<div class="f-rule" style="left:339px;top:2686px;width:185px"></div>
<p class="f-small" style="left:339px;top:2698px;width:200px"><span style="color:#fff">Hearthline Insurance</span><br>Lorem ipsum dolor sit amet, consectetur adipiscing elit, sed do eiusmod</p>
<svg class="abs" style="left:339px;top:2780px" width="14" height="14" viewBox="0 0 24 24"><path d="M6 2h4l2 5-3 2a12 12 0 0 0 6 6l2-3 5 2v4a2 2 0 0 1-2 2A18 18 0 0 1 4 4a2 2 0 0 1 2-2z" fill="#2f5fb3"/></svg>
<p class="abs" style="left:360px;top:2779px;font-size:14px;color:#ddd">123.456.7890</p>
<svg class="abs" style="left:339px;top:2814px" width="14" height="12" viewBox="0 0 24 18"><rect x="1" y="1" width="22" height="16" fill="#2f5fb3"/><path d="M1 1l11 9 11-9" stroke="#1c1c1c" stroke-width="2" fill="none"/></svg>
<p class="abs" style="left:360px;top:2812px;font-size:11px;color:#bbb">info@hearthline.com</p>
<h4 class="f-title" style="left:623px;top:2658px">Join Our Newsletter</h4>
<div class="f-rule" style="left:623px;top:2686px;width:215px"></div>
<p class="f-small" style="left:623px;top:2712px;width:190px">Subscribe to our Newsletter to get the latest scoop right to your inbox</p>
<div class="input" style="left:623px;top:2760px;width:172px;height:30px;background:#444;border:0;color:#ddd">Enter Your Email</div>
<div class="btn btn-red" style="left:623px;top:2803px;width:93px;height:27px;text-transform:none;font-size:12px">Subscribe</div>
<div class="abs" style="left:900px;top:2690px;width:150px;text-align:center;font-family:'Raleway',sans-serif;font-weight:600;font-size:22px;color:#bbb;line-height:30px">Hearthline</div>

<div class="copy">
  <p class="abs" style="left:141px;top:10px;font-family:'Open Sans',sans-serif;font-weight:600;font-size:11px;color:var(--white)">© 2018 Hearthlineinsurance.com. All Rights Reserved.</p>
  <span class="social" style="left:980px"></span>
  <span class="social" style="left:1008px"></span>
  <span class="social" style="left:1037px"></span>
</div>

</body>
</html>
```